Business Card for Health Food Store

I need a business card for a health food store that includes the following information.

=========
FRONT
=========

***White background***

Bright Harvest (logo)
Supplements - Health Foods - Remedies

2214 Alder Rd.
Linden Falls, CA 95321
(corner of Ferris Ln.)

707-482-3196

BrightHarvest.co
BrightHarvestGoods@mailbox-example.com

On the right side of the front of the card, use a circle type seal with 25 large in the middle. Put the dates below it.
"Celebrating 25 Years"
1997 - 2022

*DO NOT USE A PERSON'S NAME ON THE CARD*

==========
BACK
==========

***Green background***

Full logo in white along with the social logos and handles.

FB Logo / BrightHarvestShop
IG Logo / BrightHarvestShop
Twitter Logo / VisitBrightHarvest

When done I'll need the file in PSD and AI.

Target Market(s)

Surrounding local community

Industry/Entity Type

Retail Health Food Store

Contact Information for Business Card

See brief

Requirements
Must have
• Must be double-sided

```html
<!DOCTYPE html>
<html lang="en">
<head>
<meta charset="utf-8">
<title>Bright Harvest – Business Card</title>
<link rel="stylesheet" href="https://fonts.googleapis.com/css2?family=Roboto:wght@400;500;700&family=Roboto+Condensed:wght@400;700&display=swap">
<style>
  :root {
    --stage: #8c8c8c;
    --green: #58b133;
    --green-soft: #adcd96;
    --mist: #e2e7eb;
    --white: #ffffff;
    --ink: #333638;
    --black: #111111;
    --charcoal: #2f3234;
  }
  * { box-sizing: border-box; margin: 0; padding: 0; }
  html, body { width: 1200px; height: 1013px; overflow: hidden; background: var(--stage); }
  .canvas { position: relative; width: 1200px; height: 1013px; }

  .card {
    position: absolute; top: 87px; width: 504px; height: 840px;
    border-radius: 34px; overflow: hidden;
  }
  .card--front { left: 79px; background: var(--mist); }
  .card--back { left: 624px; background: var(--green); }
  .card__shapes { position: absolute; inset: 0; }

  .centered { position: absolute; left: 0; width: 100%; text-align: center; white-space: nowrap; }

  .banner__name {
    top: 54px; font-family: "Roboto Condensed", sans-serif; font-weight: 700;
    font-size: 54px; color: var(--white); letter-spacing: 0.5px; line-height: 1;
  }
  .banner__tagline {
    top: 114px; font-family: "Roboto Condensed", sans-serif; font-weight: 400;
    font-size: 19.5px; color: var(--white);
  }

  .contact { font-family: "Roboto", sans-serif; font-size: 20px; color: var(--ink); line-height: 1; }
  .contact--address { top: 331px; line-height: 19px; }
  .contact--phone { top: 385px; }
  .contact--email { top: 421px; font-size: 19px; }
  .contact--web { top: 456px; }
  .contact--handle-fb { top: 569px; }
  .contact--handle-ig { top: 605px; }

  .front-brand { top: 720px; }
  .front-brand__name {
    display: inline-flex; align-items: center; gap: 12px;
    font-family: "Roboto", sans-serif; font-weight: 700; font-size: 36px; color: var(--black); line-height: 1;
  }
  .front-brand__dot { width: 44px; height: 44px; border-radius: 50%; background: var(--green); }
  .front-brand__tagline {
    margin-top: 6px; padding-left: 56px;
    font-family: "Roboto Condensed", sans-serif; font-weight: 700; font-size: 13px;
    color: var(--green); letter-spacing: 0.6px;
  }

  .back-brand__mark {
    position: absolute; left: 187px; top: 262px; width: 130px; height: 130px;
    border-radius: 50%; background: var(--mist);
  }
  .back-brand__name {
    top: 410px; font-family: "Roboto", sans-serif; font-weight: 700; font-size: 56px;
    color: var(--mist); line-height: 1;
  }
  .back-brand__tagline {
    top: 466px; font-family: "Roboto Condensed", sans-serif; font-weight: 700; font-size: 18.5px;
    color: var(--mist); letter-spacing: 1px;
  }
  .anniversary {
    top: 716px; font-family: "Roboto", sans-serif; font-weight: 500; font-size: 27px;
    color: var(--white); line-height: 33px;
  }
</style>
</head>
<body>
<div class="canvas">

  <section class="card card--front" aria-label="Card front">
    <svg class="card__shapes" width="504" height="840" viewBox="0 0 504 840">
      <path fill="var(--green-soft)" d="M0 237 L25 251 Q49 265 49 300 V613 Q49 648 25 662 L0 676 Z"/>
      <path fill="var(--green-soft)" d="M504 237 L479 251 Q455 265 455 300 V613 Q455 648 479 662 L504 676 Z"/>
      <path fill="var(--green)" d="M39 0 H464 V145 L305 232 Q252 258 199 232 L39 145 Z"/>
      <path fill="none" stroke="var(--white)" stroke-width="3" d="M50 0 V137 L207 220 Q252 241 297 220 L454 137 V0"/>

      <g class="icon-row">
        <circle cx="180" cy="299" r="15" fill="var(--green)"/>
        <path fill="var(--white)" d="M180 290 a6 6 0 0 1 6 6 c0 4 -6 11 -6 11 c0 0 -6 -7 -6 -11 a6 6 0 0 1 6 -6 z"/>
        <circle cx="180" cy="296" r="2.2" fill="var(--green)"/>
        <circle cx="227" cy="299" r="15" fill="var(--green)"/>
        <path fill="var(--white)" d="M221 292 l3 -1 l2 5 l-2 2 q2 4 6 6 l2 -2 l5 2 l-1 3 q-1 2 -4 1 q-9 -3 -12 -12 q-1 -3 1 -4 z"/>
        <circle cx="275" cy="299" r="15" fill="var(--green)"/>
        <rect x="267" y="294" width="16" height="11" rx="1.5" fill="none" stroke="var(--white)" stroke-width="1.6"/>
        <path d="M272 294 v-2.5 h6 v2.5 M267 299 h16" fill="none" stroke="var(--white)" stroke-width="1.6"/>
        <circle cx="323" cy="299" r="15" fill="var(--green)"/>
        <g fill="none" stroke="var(--white)" stroke-width="1.5">
          <circle cx="323" cy="299" r="8"/>
          <ellipse cx="323" cy="299" rx="3.5" ry="8"/>
          <path d="M315 299 h16 M316.5 295 h13 M316.5 303 h13"/>
        </g>
      </g>

      <g fill="var(--green)">
        <path d="M86 497 l5 5 l-5 5 l-5 -5 z"/><path d="M104 497 l5 5 l-5 5 l-5 -5 z"/>
        <path d="M122 497 l5 5 l-5 5 l-5 -5 z"/><path d="M140 497 l5 5 l-5 5 l-5 -5 z"/>
        <path d="M158 497 l5 5 l-5 5 l-5 -5 z"/><path d="M176 497 l5 5 l-5 5 l-5 -5 z"/>
        <path d="M194 497 l5 5 l-5 5 l-5 -5 z"/><path d="M212 497 l5 5 l-5 5 l-5 -5 z"/>
        <path d="M230 497 l5 5 l-5 5 l-5 -5 z"/><path d="M248 497 l5 5 l-5 5 l-5 -5 z"/>
        <path d="M266 497 l5 5 l-5 5 l-5 -5 z"/><path d="M284 497 l5 5 l-5 5 l-5 -5 z"/>
        <path d="M302 497 l5 5 l-5 5 l-5 -5 z"/><path d="M320 497 l5 5 l-5 5 l-5 -5 z"/>
        <path d="M338 497 l5 5 l-5 5 l-5 -5 z"/><path d="M356 497 l5 5 l-5 5 l-5 -5 z"/>
        <path d="M374 497 l5 5 l-5 5 l-5 -5 z"/><path d="M392 497 l5 5 l-5 5 l-5 -5 z"/>
        <path d="M410 497 l5 5 l-5 5 l-5 -5 z"/>
      </g>

      <circle cx="227" cy="539" r="15" fill="var(--green)"/>
      <circle cx="275" cy="539" r="15" fill="var(--green)"/>

      <path fill="var(--green)" d="M0 740 C40 690 80 673 140 673 H364 C424 673 464 690 504 740 V840 H0 Z"/>
      <path fill="var(--mist)" d="M0 750 C42 698 82 679 142 679 H362 C422 679 462 698 504 750 V840 H0 Z"/>
      <path fill="var(--white)" d="M0 762 C45 706 85 687 145 687 H359 C419 687 459 706 504 762 V840 H0 Z"/>
    </svg>

    <div class="centered banner__name">BRIGHT HARVEST</div>
    <div class="centered banner__tagline">SUPPLEMENTS - HEALTH FOODS - REMEDIES</div>

    <div class="centered contact contact--address">2214 Alder Rd.<br>Linden Falls, CA 95321</div>
    <div class="centered contact contact--phone">707-482-3196</div>
    <div class="centered contact contact--email">BrightHarvestGoods@mailbox-example.com</div>
    <div class="centered contact contact--web">BrightHarvest.co</div>
    <div class="centered contact contact--handle-fb">BrightHarvestShop</div>
    <div class="centered contact contact--handle-ig">BrightHarvestShop</div>

    <div class="centered front-brand">
      <div class="front-brand__name"><span class="front-brand__dot"></span>Bright Harvest</div>
      <div class="front-brand__tagline">SUPPLEMENTS • HEALTH FOODS • REMEDIES</div>
    </div>
  </section>

  <section class="card card--back" aria-label="Card back">
    <svg class="card__shapes" width="504" height="840" viewBox="0 0 504 840">
      <path fill="var(--white)" d="M0 728 C40 690 80 671 140 671 H364 C424 671 464 690 504 728 V840 H0 Z"/>
      <path fill="var(--green)" d="M0 736 C42 698 82 679 142 679 H362 C422 679 462 698 504 736 V840 H0 Z"/>
      <path fill="var(--charcoal)" d="M0 752 C45 706 85 686 145 686 H359 C419 686 459 706 504 752 V840 H0 Z"/>
    </svg>

    <div class="back-brand__mark"></div>
    <div class="centered back-brand__name">Bright Harvest</div>
    <div class="centered back-brand__tagline">SUPPLEMENTS • HEALTH FOODS • REMEDIES</div>

    <div class="centered anniversary">Celebrating 25 Years<br>1997 - 2022</div>
  </section>

</div>
</body>
</html>
```